KBT Business Cards

We require business cards for our business. We would like a matte black back to the card, with our logo centred in the middle. The front side of the card is open to design.

Target Market(s)

Clients looking for legal services (professional)

Industry/Entity Type

Legal

Contact Information for Business Card

Doran Kelbrath
Partner
Mobile: 0461 738 524
Email: doran@kbtlaw.co
Website: www.kbtlaw.co
Level 3, 118 Wendmore Street
Sydney NSW 2000

Font styles to use
Other font styles liked:
• Avenir

Colors
f04a50
ffffff
1b1b1b

Requirements
Must have
• Black back with logo included in the centre of the card.
• Our font is Avenir.

```html
<!DOCTYPE html>
<html lang="en">
<head>
<meta charset="utf-8">
<title>KBT Business Cards</title>
<link href="https://fonts.googleapis.com/css2?family=Nunito+Sans:wght@400;700;800&display=swap" rel="stylesheet">
<style>
  :root {
    --stage: #222222;
    --card-black: #1b1b1b;
    --card-white: #f7f7f7;
    --ink: #111111;
    --accent: #f04a50;
    --silver: #cfcfcf;
    --muted-square: #3a3a3a;
  }
  * { margin: 0; padding: 0; box-sizing: border-box; }
  html, body { width: 980px; height: 1200px; overflow: hidden; }
  body {
    background: var(--stage);
    font-family: "Nunito Sans", "Avenir", sans-serif;
    position: relative;
  }
  .card {
    position: absolute;
    left: 126px;
    width: 756px;
    height: 432px;
  }
  .card--back { top: 101px; background: var(--card-black); }
  .card--front { top: 641px; background: var(--card-white); }

  .brand {
    position: absolute;
    display: flex;
    align-items: center;
    gap: 26px;
  }
  .brand__square {
    width: 64px;
    height: 64px;
  }
  .brand__name {
    font-weight: 800;
    text-transform: uppercase;
    line-height: 1.05;
  }
  .card--back .brand {
    left: 50%;
    top: 50%;
    transform: translate(-50%, -50%);
  }
  .card--back .brand__square { background: var(--muted-square); width: 96px; height: 96px; }
  .card--back .brand__name { color: var(--silver); font-size: 36px; }

  .card--front .brand { left: 72px; top: 172px; gap: 20px; }
  .card--front .brand__square { background: var(--accent); width: 60px; height: 60px; }
  .card--front .brand__name { color: var(--ink); font-size: 21px; }

  .contact {
    position: absolute;
    left: 425px;
    top: 78px;
    color: var(--ink);
  }
  .contact__name {
    font-size: 30px;
    font-weight: 700;
    letter-spacing: 0.5px;
    line-height: 1;
    text-transform: uppercase;
  }
  .contact__surname { color: var(--accent); }
  .contact__role {
    margin-top: 10px;
    font-size: 16px;
    letter-spacing: 1px;
  }
  .contact__rule {
    width: 68px;
    height: 2px;
    background: var(--ink);
    margin: 17px 0 20px;
  }
  .contact__list { list-style: none; }
  .contact__item {
    display: flex;
    align-items: center;
    gap: 14px;
    font-size: 17px;
    letter-spacing: 0.6px;
    line-height: 26px;
  }
  .contact__icon { width: 13px; height: 13px; flex: none; }
  .contact__address {
    font-size: 17px;
    letter-spacing: 0.8px;
    line-height: 28px;
  }
</style>
</head>
<body>
  <section class="card card--back" aria-label="Card back">
    <div class="brand">
      <span class="brand__square"></span>
      <span class="brand__name">Kelbrath<br>Bellamy Tarrow<br>Legal</span>
    </div>
  </section>

  <section class="card card--front" aria-label="Card front">
    <div class="brand">
      <span class="brand__square"></span>
      <span class="brand__name">Kelbrath<br>Bellamy Tarrow<br>Legal</span>
    </div>

    <div class="contact">
      <h1 class="contact__name">Doran <span class="contact__surname">Kelbrath</span></h1>
      <p class="contact__role">Partner</p>
      <div class="contact__rule"></div>
      <ul class="contact__list">
        <li class="contact__item">
          <svg class="contact__icon" viewBox="0 0 24 24"><path fill="#f04a50" d="M6.6 10.8a15.1 15.1 0 0 0 6.6 6.6l2.2-2.2c.3-.3.7-.4 1-.2 1.1.4 2.3.6 3.6.6.6 0 1 .4 1 1V20c0 .6-.4 1-1 1A17 17 0 0 1 3 4c0-.6.4-1 1-1h3.5c.6 0 1 .4 1 1 0 1.3.2 2.5.6 3.6.1.3 0 .7-.2 1z"/></svg>
          0461 738 524
        </li>
        <li class="contact__item">
          <svg class="contact__icon" viewBox="0 0 24 24"><path fill="#f04a50" d="M2 5h20v3l-10 6L2 8zm0 5 10 6 10-6v9H2z"/></svg>
          doran@kbtlaw.co
        </li>
        <li class="contact__item">
          <svg class="contact__icon" viewBox="0 0 24 24"><g fill="none" stroke="#f04a50" stroke-width="2"><circle cx="12" cy="12" r="10"/><ellipse cx="12" cy="12" rx="4" ry="10"/><path d="M2 12h20M4 7h16M4 17h16"/></g></svg>
          www.kbtlaw.co
        </li>
      </ul>
      <div class="contact__rule"></div>
      <address class="contact__address" style="font-style: normal;">
        Level 3, 118 Wendmore Street<br>Sydney NSW 2000
      </address>
    </div>
  </section>
</body>
</html>
```